Business card for law firm

Need business card for new law firm. Think confident, authoritative, conservative, but not stuffy or old-fashioned.

Contact Information for Business Card

Content for card - logo (uploaded), plus the following:

Paul Whitcombe (larger font)
Managing Partner (larger font, but not as large as name)
Level 9, 7 Ferris Lane
Sydney NSW 2000
Main Tel 02 9364 2710
Direct Tel 02 8472 3159
Email paul@qvlegal.com.au
www.qvlegal.com.au

Letterhead design should include logo plus:
Level 9, 7 Ferris Lane
Sydney NSW 2000
Tel 02 8472 3159
www.qvlegal.com.au

```html
<!DOCTYPE html>
<html lang="en">
<head>
<meta charset="utf-8">
<title>Quayvale Legal — Business Card</title>
<link rel="stylesheet" href="https://fonts.googleapis.com/css2?family=Cinzel:wght@400;500&family=Jost:wght@400;600&display=swap">
<style>
  :root {
    --backdrop: #4a4b4e;
    --navy: #0b1f5c;
    --navy-light: #17348a;
    --paper: #e7e7e9;
    --ink: #1a1a1a;
    --ink-soft: #2b2b2b;
    --rule: #3a3a3a;
    --white: #ffffff;
  }
  * { margin: 0; padding: 0; box-sizing: border-box; }
  html, body { width: 1200px; height: 1000px; overflow: hidden; }
  body { background: var(--backdrop); position: relative; font-family: "Jost", sans-serif; }

  .card {
    position: absolute;
    width: 660px;
    height: 400px;
    border-radius: 26px;
    overflow: hidden;
    box-shadow: 0 12px 30px rgba(0,0,0,0.35);
  }

  /* Front */
  .card--front {
    left: 300px; top: 60px;
    background: linear-gradient(135deg, var(--navy) 0%, var(--navy-light) 100%);
    color: var(--white);
    text-align: center;
  }
  .brand { position: absolute; left: 0; right: 0; top: 90px; }
  .brand__square {
    width: 58px; height: 58px; margin: 0 auto 22px;
    background: var(--white);
  }
  .brand__name {
    font-family: "Cinzel", serif; font-weight: 400;
    font-size: 50px; letter-spacing: 3px; line-height: 1;
  }
  .brand__tag {
    font-family: "Cinzel", serif; font-weight: 400;
    font-size: 18px; letter-spacing: 18px; margin-top: 10px; padding-left: 18px;
  }
  .card--front .site {
    position: absolute; left: 0; right: 0; bottom: 48px;
    font-size: 16px; letter-spacing: 1px;
  }

  /* Back */
  .card--back {
    left: 240px; top: 530px;
    background: var(--paper);
  }
  .swoosh { position: absolute; left: 0; bottom: 0; width: 660px; height: 400px; }
  .card--back .brand { top: 70px; left: 30px; right: auto; width: 330px; text-align: center; color: var(--ink); }
  .card--back .brand__square { background: var(--navy); width: 52px; height: 52px; margin-bottom: 18px; }
  .card--back .brand__name { font-size: 40px; letter-spacing: 2px; }
  .card--back .brand__tag { font-size: 14px; letter-spacing: 15px; padding-left: 15px; }

  .divider { position: absolute; left: 370px; top: 70px; width: 2px; height: 190px; background: var(--rule); }
  .contact { position: absolute; left: 388px; top: 62px; color: var(--ink-soft); font-size: 15px; line-height: 1.35; }
  .contact__name { color: var(--navy); font-weight: 600; font-size: 22px; letter-spacing: 0.5px; line-height: 1.1; }
  .contact__role { font-size: 16px; margin-bottom: 10px; }
  .contact__address { margin-bottom: 10px; }
  .contact__label { color: var(--navy); font-weight: 600; }
  .contact__row { display: flex; align-items: center; gap: 6px; }
  .contact__row svg { width: 13px; height: 13px; flex: none; }
  .contact__site b { color: var(--navy); font-weight: 600; }
</style>
</head>
<body>

  <section class="card card--front">
    <div class="brand">
      <div class="brand__square"></div>
      <div class="brand__name">QUAYVALE</div>
      <div class="brand__tag">LEGAL</div>
    </div>
    <div class="site">www.qvlegal.com.au</div>
  </section>

  <section class="card card--back">
    <svg class="swoosh" viewBox="0 0 660 400" aria-hidden="true">
      <path d="M0 290 C 150 330, 330 355, 660 340 L660 400 L0 400 Z" fill="var(--navy)"/>
      <path d="M0 270 C 120 300, 200 335, 300 370 C 200 345, 90 315, 0 300 Z" fill="var(--ink)"/>
    </svg>

    <div class="brand">
      <div class="brand__square"></div>
      <div class="brand__name">QUAYVALE</div>
      <div class="brand__tag">LEGAL</div>
    </div>

    <div class="divider"></div>

    <div class="contact">
      <div class="contact__name">PAUL WHITCOMBE</div>
      <div class="contact__role">Managing Partner</div>
      <div class="contact__address">Level 9, 7 Ferris Lane<br>Sydney NSW 2000</div>
      <div><span class="contact__label">Main Tel</span> 02 9364 2710</div>
      <div><span class="contact__label">Direct Tel</span> 02 8472 3159</div>
      <div class="contact__row">
        <svg viewBox="0 0 14 14" aria-hidden="true"><rect x="0.5" y="2.5" width="13" height="9" rx="1" fill="var(--navy)"/><path d="M1 3 L7 8 L13 3" stroke="#fff" stroke-width="1.2" fill="none"/></svg>
        paul@qvlegal.com.au
      </div>
      <div class="contact__row contact__site">
        <svg viewBox="0 0 14 14" aria-hidden="true"><circle cx="7" cy="7" r="6" fill="var(--navy)"/><path d="M1 7 H13 M7 1 C3.5 4 3.5 10 7 13 M7 1 C10.5 4 10.5 10 7 13" stroke="#fff" stroke-width="0.9" fill="none"/></svg>
        <span>www.<b>qvlegal.com.au</b></span>
      </div>
    </div>
  </section>

</body>
</html>
```